KRT Engineering Business Card Design

We’re looking for an elegant, clean, and timeless business card design that communicates experience, capability, and reliability.

KRT Engineering was established in 1995 , we are a Government Contracting company providing Professional Services to the Office of Frontier Affairs, Harbor Protection and the Vantage Collective. Our capabilities include: Acquisition & Program Management; Intelligence & Security Operations; Cyber, IT & Network Operations; Lifecycle Logistics & Asset Readiness; C5ISR Systems Engineering & Sustainment.

We want the card to reflect a straightforward, confident approach to business. The design should feel polished and professional without being flashy or overly corporate.

Design Direction
Clean, sophisticated, and uncluttered
Elegant but understated
Strong typography and thoughtful spacing
A timeless aesthetic rather than something overly trendy
Confident and established, with a sense of substance
Easy to read and practical in a real-world business setting

The overall impression should be: “These are experienced professionals who know what they’re doing, do what they say, and can be relied upon.”

We’re open to creative interpretations. The finished card should feel distinctive through its typography, proportions, layout, and attention to detail rather than through excessive graphics or visual effects.

We’re looking for a design that would make a potential client immediately feel that they’re dealing with a capable, trustworthy, and established company.

Company Colors: Navy and Gold/Yellow (but you do not need to use these colors on the card)
Company Name: KRT Engineering Associates, Inc. (known as KRT Engineering)
Website: krtengineering.com
Company Logo: Navy & Gold (other variations attached)

```html
<!DOCTYPE html>
<html lang="en">
<head>
<meta charset="utf-8">
<title>KRT Engineering Business Card</title>
<link rel="stylesheet" href="https://fonts.googleapis.com/css2?family=Arimo:wght@400;700&display=swap">
<style>
  :root {
    --backdrop: #1b1b1c;
    --navy: #1f2a5f;
    --ink: #ffffff;
    --rule: rgba(255,255,255,0.85);
  }
  * { margin: 0; padding: 0; box-sizing: border-box; }
  html, body {
    width: 1200px; height: 1059px; overflow: hidden;
    background: var(--backdrop);
    font-family: "Arimo", Arial, sans-serif;
    color: var(--ink);
  }
  .canvas { position: relative; width: 1200px; height: 1059px; }
  .card {
    position: absolute;
    background: var(--navy);
    border-radius: 18px;
  }
  .card-front { left: 257px; top: 90px; width: 687px; height: 389px; }
  .card-back  { left: 254px; top: 547px; width: 693px; height: 393px; }

  .front-wordmark {
    position: absolute; left: 120px; top: 133px; width: 200px;
    text-align: center;
    font-weight: 700; font-size: 66px; line-height: 1; letter-spacing: -1px;
  }
  .divider {
    position: absolute; left: 343px; top: 122px;
    width: 1px; height: 147px; background: var(--rule);
  }
  .contact { position: absolute; left: 372px; top: 120px; }
  .person-name { font-weight: 700; font-size: 22px; line-height: 1; }
  .person-title { font-size: 17.5px; line-height: 1; margin-top: 6px; }
  .contact-list { list-style: none; margin-top: 22px; }
  .contact-list li {
    display: flex; align-items: center;
    font-size: 17.5px; line-height: 1; height: 31px;
  }
  .contact-list svg { width: 13px; height: 13px; margin-right: 9px; flex: none; }

  .back-wordmark {
    position: absolute; left: 0; right: 0; top: 140px;
    text-align: center;
    font-weight: 700; font-size: 116px; line-height: 1; letter-spacing: -2px;
  }
</style>
</head>
<body>
<main class="canvas">
  <section class="card card-front" aria-label="Card front">
    <div class="front-wordmark">KRT</div>
    <div class="divider"></div>
    <div class="contact">
      <h1 class="person-name">Elena M. Whitaker</h1>
      <p class="person-title">Principal Engineer</p>
      <ul class="contact-list">
        <li>
          <svg viewBox="0 0 16 16" aria-hidden="true"><path fill="#fff" d="M3.2 1.5 5.6 1l1.3 3.2-1.6 1.2a8 8 0 0 0 5.3 5.3l1.2-1.6 3.2 1.3-.5 2.4c-.2.7-.8 1.2-1.5 1.2C7 14 2 9 2 3c0-.7.5-1.3 1.2-1.5z"/></svg>
          (555) 208-3914
        </li>
        <li>
          <svg viewBox="0 0 16 16" aria-hidden="true"><path fill="#fff" d="M1 5.5 8 1l7 4.5V14H1z"/><path fill="none" stroke="#1f2a5f" stroke-width="1.3" d="M1.5 6 8 10l6.5-4"/></svg>
          e.w@krtengineering.com
        </li>
        <li>
          <svg viewBox="0 0 16 16" aria-hidden="true"><circle cx="8" cy="8" r="7" fill="#fff"/><path fill="#1f2a5f" d="M5 3.5c1.5.3 2 1.5 1.2 2.6-.8 1-2.2.6-2.4 2 1.5.2 2.4 1.2 2 3C4.2 10.4 3 9 3 7.5c0-1.6.8-3.1 2-4zM10 6c1.2-.4 2.6.3 3 1.6-.2 1.9-1.2 3.5-2.8 4.3.3-1.6-1.2-2.2-1.4-3.3C8.6 7.5 9 6.4 10 6z"/></svg>
          krtengineering.com
        </li>
      </ul>
    </div>
  </section>

  <section class="card card-back" aria-label="Card back">
    <div class="back-wordmark">KRT</div>
  </section>
</main>
</body>
</html>
```